Vigor Health & Fitness Website selling saunas and Cold tubs

www.dockvaultguys.com, www.frostlanterguys, www.chillharborguys
Design a website
We are selling saunas, infrared saunas, cold plunge tubs, and massage chairs to financially successful MEN.
We want professional, simple, masculine with a touch of sexy.
One section for each… saunas, cold plunge tubs, massage chairs.
Each will have at least two buy links to their affiliate/supplier/store.
The landing page / opening page / needs big & bold; a full screen image? a great picture showing the warmth of a sauna? Need your ideas
The pictures are everything.

The Website for our book
https://maebelsvigorguys.com/

Coding

Coded - Design and coding required

Number of Pages Required

1 page

Requirements
Must have
• Great pictures

```html
<!DOCTYPE html>
<html lang="en">
<head>
<meta charset="utf-8">
<title>Maebel Vigor Fitness for Men – Light and Dark Themes</title>
<link href="https://fonts.googleapis.com/css2?family=Oswald:wght@500;600;700&family=Inter:wght@400;500;600;700&display=swap" rel="stylesheet">
<style>
:root{
  --orange:#f37021;
  --red:#e8401c;
  --grad:linear-gradient(90deg,#f58220,#e8401c);
  --canvas:#4a4a4a;
  --ink:#141414;
  --body:#6b6b6b;
  --white:#ffffff;
  --night:#050505;
  --band:#121212;
  --card-light:#ffffff;
  --card-dark:#1b1b1b;
  --star:#f5b400;
}
*{box-sizing:border-box;margin:0;padding:0}
html,body{width:763px;height:1200px;overflow:hidden;background:var(--canvas)}
body{position:relative;font-family:"Inter",Arial,sans-serif}
.page{position:absolute;top:23px;width:344px;height:1145px;overflow:hidden}
.page--light{left:26px;--bg:#fff;--text:var(--ink);--muted:var(--body);--card:var(--card-light);--cardline:#e4e4e4;background:var(--bg)}
.page--dark{left:393px;--bg:var(--night);--text:#fff;--muted:#cfcfcf;--card:var(--card-dark);--cardline:#262626;background:var(--bg)}
.abs{position:absolute}
.display{font-family:"Oswald",Impact,sans-serif;font-weight:600;text-transform:uppercase;letter-spacing:.1px;color:var(--text)}
.accent{color:var(--red)}
.accent-o{color:var(--orange)}

/* header */
.site-header{left:0;top:0;width:344px;height:24px;background:var(--bg);z-index:3}
.site-header__name{left:41px;top:10px;font-size:3.9px;font-weight:500;color:var(--text)}
.brand-badge{left:149px;top:0;width:46px;height:46px;border-radius:50%;background:var(--bg);display:flex;align-items:center;justify-content:center;z-index:4}
.brand-badge span{display:block;width:34px;text-align:center;font-family:"Oswald",sans-serif;font-weight:600;font-size:4.2px;line-height:5px;color:var(--text)}
.btn{position:absolute;height:10px;border-radius:6px;display:flex;align-items:center;justify-content:center;gap:2px;font-size:3.7px;font-weight:700;text-transform:uppercase;white-space:nowrap}
.btn--primary{background:var(--grad);color:#fff}
.btn--ghost{border:.7px solid var(--text);color:var(--text);background:transparent}
.btn i{display:inline-block;width:3.6px;height:3.6px;border-radius:50%;background:currentColor;position:relative}
.btn--primary i{background:#fff}
.btn i::after{content:"";position:absolute;left:1px;top:1px;width:1.2px;height:1.2px;border-right:.5px solid var(--orange);border-top:.5px solid var(--orange);transform:rotate(45deg)}
.btn--ghost i::after{border-color:var(--bg)}
.header-btn{left:268px;top:6px;width:35px;height:11px}

/* hero */
.hero{left:0;top:24px;width:344px;height:200px}
.page--light .hero{background:radial-gradient(ellipse at 70% 40%,#e7c3a8 0,#c99a7c 22%,#9fb7c2 45%,#dfe8ec 70%,#f4f6f7 100%)}
.page--dark .hero{background:radial-gradient(ellipse at 72% 45%,#a9745a 0,#5a3a2b 18%,#1f3d45 42%,#0c1a1e 70%,#050607 100%)}
.hero__kicker{left:41px;top:64px;font-size:3.9px;font-weight:600;color:var(--text)}
.hero__title{left:41px;top:75px;font-size:12.2px;line-height:15px;font-weight:600}
.page--dark .hero__title,.page--dark .hero__kicker,.page--dark .hero__lead{color:#fff}
.hero__lead{left:41px;top:107px;width:150px;font-size:3.9px;line-height:7px;font-weight:500;color:var(--text)}
.hero__btn{left:41px;top:127px;width:52px;height:13px;font-size:4px}
.hero-wave{left:0;top:186px;width:344px;height:60px}

/* product sections */
.product__media{position:absolute;width:114px;height:114px;border-radius:50%}
.product__ring{position:absolute;width:124px;height:124px;border-radius:50%;border:3px solid transparent}
.ring--left{border-left-color:var(--orange);border-bottom-color:var(--red);transform:rotate(20deg)}
.ring--right{border-right-color:var(--red);border-top-color:var(--orange);transform:rotate(20deg)}
.media--sauna{background:radial-gradient(circle at 50% 45%,#f3e7da 0,#d9a071 30%,#b06a3a 60%,#6e3b1e 100%)}
.media--plunge{background:radial-gradient(circle at 50% 40%,#d9c2ad 0,#6fa6b8 28%,#2d7e95 55%,#0e4a5c 100%)}
.media--chair{background:radial-gradient(circle at 50% 45%,#d8a88a 0,#b57c5d 25%,#2e3a3d 60%,#121617 100%)}
.product__title{position:absolute;font-size:10.5px;line-height:12px}
.product__sub{position:absolute;font-size:4.2px;font-weight:500;color:var(--text)}
.product__body{position:absolute;width:131px;font-size:3.5px;line-height:6.6px;text-align:justify;color:var(--muted)}
.btn--sm{width:34px}
.btn--supplier{width:62px}

/* benefits band */
.benefits{left:0;top:602px;width:344px;height:151px;background:var(--band);overflow:hidden}
.benefits__figure-left{left:0;top:57px;width:100px;height:94px;background:radial-gradient(ellipse at 45% 30%,#b08a73 0,#6d5649 22%,#3f6f86 48%,#9ec7dc 72%,#1b2a33 100%)}
.benefits__figure-right{left:238px;top:65px;width:106px;height:86px;background:radial-gradient(ellipse at 55% 50%,#e8d5bf 0,#c9a98a 30%,#5a4a3e 60%,rgba(18,18,18,0) 80%)}
.benefits__title{left:0;top:17px;width:344px;text-align:center;font-size:9.6px;line-height:13.6px;color:#fff}
.benefits__list{left:0;top:51px;width:344px;text-align:center;color:#fff;font-size:4.4px;line-height:7.35px;font-weight:500}
.benefits__note{left:0;top:101px;width:344px;text-align:center;color:#fff;font-size:6.2px;font-weight:500}
.benefits__btn{left:154px;top:123px;width:35px;height:11px}

/* testimonials */
.testimonials__title{left:0;top:772px;width:344px;text-align:center;font-size:10.6px}
.quote{position:absolute;width:122px;height:37px;background:var(--card);border:.6px solid var(--cardline);box-shadow:0 .5px 1.5px rgba(0,0,0,.08);padding:7px 6px 0}
.quote__stars{position:absolute;top:4px;left:0;width:100%;text-align:center;color:var(--star);font-size:3.6px;letter-spacing:.5px}
.quote__mark{position:absolute;font-family:Georgia,serif;font-weight:700;color:var(--red);font-size:7px;line-height:7px}
.quote__mark--open{left:5px;top:2px}
.quote__mark--close{right:5px;bottom:-1px}
.quote p{font-size:2.85px;line-height:5.4px;color:var(--muted);text-align:center}
.testimonials__note{left:0;top:965px;width:344px;text-align:center;font-size:6.2px;font-weight:500;color:var(--text)}
.testimonials__btn{left:154px;top:983px;width:35px;height:11px}

/* footer */
.footer-wave{left:0;top:990px;width:344px;height:50px}
.site-footer{left:0;top:1028px;width:344px;height:117px;background:var(--band)}
.footer__label{position:absolute;font-size:4.6px;font-weight:700;color:#fff;text-transform:uppercase}
.field{position:absolute;left:41px;width:72px;height:11px;background:#fff;font-size:3.2px;color:#aaa;padding:3.6px 5px}
.submit{left:41px;top:91px;width:72px;height:12px;border-radius:0;font-size:4px}
.contact-item{position:absolute;left:140px;width:80px}
.contact-item__icon{position:absolute;left:0;top:0;width:10px;height:10px;border-radius:50%;border:.6px solid #fff;display:flex;align-items:center;justify-content:center}
.contact-item__label{position:absolute;left:13px;top:0;font-size:3.8px;font-weight:600;color:#fff}
.contact-item__text{position:absolute;left:13px;top:6px;font-size:3.3px;line-height:6px;color:#ddd;white-space:nowrap}
.contact-rule{position:absolute;left:140px;width:80px;height:.5px;background:#444}
.footer-divider{position:absolute;left:220px;top:28px;width:.5px;height:85px;background:#444}
.footer-badge{left:240px;top:16px;width:54px;height:54px;border-radius:50%;background:#fff;display:flex;align-items:center;justify-content:center}
.footer-badge span{width:40px;text-align:center;font-family:"Oswald",sans-serif;font-weight:600;font-size:5.2px;line-height:6.2px;color:var(--ink)}
.social{position:absolute;top:77px;width:10px;height:10px;border-radius:50%;border:.6px solid #fff}
.copyright{left:220px;top:92px;width:100px;text-align:center;font-size:3.4px;line-height:5.4px;color:#fff}
</style>
</head>
<body>

<!-- LIGHT THEME -->
<article class="page page--light">
  <header class="site-header abs">
    <p class="site-header__name abs">MAEBEL VIGOR FITNESS FOR MEN !</p>
    <a class="btn btn--primary header-btn">Buy Now <i></i></a>
  </header>
  <div class="brand-badge abs"><span>MAEBEL VIGOR FITNESS</span></div>

  <section class="hero abs" role="img" aria-label="Smiling couple relaxing together in a bright hot tub"></section>
  <p class="hero__kicker abs">Top of the Line Health Products Exclusively for the Financially Successful</p>
  <h1 class="hero__title display abs">Dramatically Improve Your<br><span class="accent">Health</span> Without <span class="accent">Exercise</span></h1>
  <p class="hero__lead abs">Successful Men Recognize the Importance of Their Health and Make it a Priority.&nbsp; It’s Your Time.&nbsp; You’ve Earned it.</p>
  <a class="btn btn--primary hero__btn abs">Buy Now <i></i></a>
  <svg class="hero-wave abs" viewBox="0 0 344 60" preserveAspectRatio="none">
    <path d="M0 26 C60 14 140 12 230 34 C280 46 320 30 344 10 L344 60 L0 60 Z" fill="#fff"/>
    <defs><linearGradient id="gl1" x1="0" x2="1"><stop offset="0" stop-color="#f58220"/><stop offset="1" stop-color="#e8401c"/></linearGradient></defs>
    <path d="M108 8 C160 10 185 38 235 40 C285 42 320 24 344 6 C322 30 288 50 235 50 C182 50 160 20 108 8 Z" fill="url(#gl1)"/>
  </svg>

  <!-- Saunas -->
  <div class="product__ring ring--left abs" style="left:33px;top:216px"></div>
  <div class="product__media media--sauna" style="left:38px;top:221px" role="img" aria-label="Couple in white robes sitting in a wooden sauna"></div>
  <h2 class="product__title display" style="left:172px;top:238px">Sau<span class="accent">nas</span></h2>
  <p class="product__sub" style="left:172px;top:256px">Lorem ipsum dolor sit amet, consectetur adipiscing.</p>
  <p class="product__body" style="left:172px;top:266px">Sed ut perspiciatis unde omnis iste natus error sit voluptatem accusantium doloremque laudantium, totam rem aperiam, eaque ipsa quae ab illo inventore veritatis et quasi architecto beatae vitae dicta sunt explicabo. Nemo enim ipsam voluptatem quia voluptas sit aspernatur aut odit aut fugit, sed quia consequuntur.</p>
  <a class="btn btn--primary btn--sm" style="left:172px;top:309px">Buy Now <i></i></a>
  <a class="btn btn--ghost btn--supplier" style="left:213px;top:309px">Buy From Supplier <i></i></a>

  <!-- Cold plunge -->
  <div class="product__ring ring--right abs" style="left:180px;top:336px"></div>
  <div class="product__media media--plunge" style="left:185px;top:341px" role="img" aria-label="Woman relaxing in a bubbling cold plunge tub"></div>
  <h2 class="product__title display" style="left:41px;top:358px">Cold <span class="accent-o">Plunge</span> Tubs</h2>
  <p class="product__sub" style="left:41px;top:376px">Lorem ipsum dolor sit amet, consectetur adipiscing.</p>
  <p class="product__body" style="left:41px;top:386px">Sed ut perspiciatis unde omnis iste natus error sit voluptatem accusantium doloremque laudantium, totam rem aperiam, eaque ipsa quae ab illo inventore veritatis et quasi architecto beatae vitae dicta sunt explicabo. Nemo enim ipsam voluptatem quia voluptas sit aspernatur aut odit aut fugit, sed quia consequuntur.</p>
  <a class="btn btn--primary btn--sm" style="left:41px;top:430px">Buy Now <i></i></a>
  <a class="btn btn--ghost btn--supplier" style="left:83px;top:430px">Buy From Supplier <i></i></a>

  <!-- Massage chairs -->
  <div class="product__ring ring--left abs" style="left:33px;top:457px"></div>
  <div class="product__media media--chair" style="left:38px;top:462px" role="img" aria-label="Man seated in a black massage chair"></div>
  <h2 class="product__title display" style="left:172px;top:478px">Massage <span class="accent">Chairs</span></h2>
  <p class="product__sub" style="left:172px;top:496px">Lorem ipsum dolor sit amet, consectetur adipiscing.</p>
  <p class="product__body" style="left:172px;top:506px">Sed ut perspiciatis unde omnis iste natus error sit voluptatem accusantium doloremque laudantium, totam rem aperiam, eaque ipsa quae ab illo inventore veritatis et quasi architecto beatae vitae dicta sunt explicabo. Nemo enim ipsam voluptatem quia voluptas sit aspernatur aut odit aut fugit, sed quia consequuntur.</p>
  <a class="btn btn--primary btn--sm" style="left:172px;top:549px">Buy Now <i></i></a>
  <a class="btn btn--ghost btn--supplier" style="left:211px;top:548px">Buy From Supplier <i></i></a>

  <!-- Benefits -->
  <section class="benefits abs">
    <div class="benefits__figure-left abs" role="img" aria-label="Man soaking in an ice bath"></div>
    <div class="benefits__figure-right abs" role="img" aria-label="Woman reclining in a massage chair"></div>
    <h2 class="benefits__title display abs">When there’s no time for exercise. Use <span class="accent-o">Hot,</span> <span class="accent">Cold,</span> or<br><span class="accent-o">Massage</span>. The benefits are numerous.</h2>
    <p class="benefits__list abs">Relieve Stress&nbsp; -&nbsp; Detox Your Pores&nbsp; -&nbsp; Sleep Better<br>Relieve Muscle Tension&nbsp; -&nbsp; Boost Energy Levels<br>Increase Testosterone&nbsp; -&nbsp; Reduce Inflammation&nbsp; -&nbsp; Increase Immunity&nbsp; Reduce<br>Depression Alleviate Joint Pain&nbsp; -&nbsp; Healthier Skin<br>Lower the Risk of Cardiovascular Disease&nbsp; -&nbsp; Increase Metabolism<br>Promote Weight Loss&nbsp; -&nbsp; A Longer &amp; Healthier Life</p>
    <p class="benefits__note abs">Specific Improvements will be Individual to You.</p>
    <a class="btn btn--primary benefits__btn">Buy Now <i></i></a>
  </section>

  <!-- Testimonials -->
  <h2 class="testimonials__title display abs"><span class="accent">Client</span> Testimonials</h2>
  <div class="quote" style="left:48px;top:796px"><span class="quote__mark quote__mark--open">“</span><span class="quote__stars">★★★★★</span><p>I climb in my sauna half asleep every morning for twenty minutes. It wakes me up better than coffee ever did. Perfect morning start.</p><span class="quote__mark quote__mark--close">”</span></div>
  <div class="quote" style="left:174px;top:796px"><span class="quote__mark quote__mark--open">“</span><span class="quote__stars">★★★★★</span><p>I love a good massage but booking one is hard. The chair is always there. I forget about work and usually drift off.</p><span class="quote__mark quote__mark--close">”</span></div>
  <div class="quote" style="left:48px;top:838px"><span class="quote__mark quote__mark--open">“</span><span class="quote__stars">★★★★★</span><p>My massage chair saves my back. I dial in a deep massage or gentle pressure whenever I need it. Worth every penny.</p><span class="quote__mark quote__mark--close">”</span></div>
  <div class="quote" style="left:174px;top:838px"><span class="quote__mark quote__mark--open">“</span><span class="quote__stars">★★★★★</span><p>I hate exercise and love my work. I have the dual plunge, hot and cold. The cold is refreshing in summer, hot in winter.</p><span class="quote__mark quote__mark--close">”</span></div>
  <div class="quote" style="left:48px;top:880px"><span class="quote__mark quote__mark--open">“</span><span class="quote__stars">★★★★★</span><p>A sauna at home is a game changer. After a long day the heat melts my stress. A mini vacation without leaving home.</p><span class="quote__mark quote__mark--close">”</span></div>
  <div class="quote" style="left:174px;top:880px"><span class="quote__mark quote__mark--open">“</span><span class="quote__stars">★★★★★</span><p>I am forty three with arthritis. My cold plunge rejuvenates my body. A natural way to deal with joint pain that actually works.</p><span class="quote__mark quote__mark--close">”</span></div>
  <div class="quote" style="left:48px;top:922px"><span class="quote__mark quote__mark--open">“</span><span class="quote__stars">★★★★★</span><p>Before my chair I walked like an old man. Every step was effort. Now I get real relief every single evening at home.</p><span class="quote__mark quote__mark--close">”</span></div>
  <div class="quote" style="left:174px;top:922px"><span class="quote__mark quote__mark--open">“</span><span class="quote__stars">★★★★★</span><p>At sixty three my body gets stiff after driving. I climb out of the car hunched. My massage chair fixes my lower back.</p><span class="quote__mark quote__mark--close">”</span></div>
  <p class="testimonials__note abs">Everything Works Better with Increased Blood Flow</p>
  <a class="btn btn--primary testimonials__btn">Buy Now <i></i></a>

  <!-- Footer -->
  <svg class="footer-wave abs" viewBox="0 0 344 50" preserveAspectRatio="none">
    <defs><linearGradient id="gl2" x1="0" x2="1"><stop offset="0" stop-color="#f58220"/><stop offset="1" stop-color="#e8401c"/></linearGradient></defs>
    <path d="M0 44 C70 14 150 8 230 26 C280 36 315 34 344 26 L344 50 L0 50 Z" fill="#121212"/>
    <path d="M2 40 C70 4 160 0 240 18 C290 28 320 26 344 20 C318 32 285 36 240 28 C160 12 80 14 2 40 Z" fill="url(#gl2)"/>
  </svg>
  <footer class="site-footer abs">
    <p class="footer__label" style="left:41px;top:20px">Contact Me</p>
    <div class="field" style="top:31px">Name</div>
    <div class="field" style="top:45px">Email</div>
    <div class="field" style="top:59px">Phone</div>
    <div class="field" style="top:73px">Message</div>
    <a class="btn btn--primary submit">Submit Now</a>
    <p class="footer__label" style="left:140px;top:20px">Contact Details</p>
    <div class="contact-item" style="top:33px"><span class="contact-item__icon"><svg width="5" height="5" viewBox="0 0 10 10"><path d="M5 0a3.5 3.5 0 0 0-3.5 3.5C1.5 6 5 10 5 10s3.5-4 3.5-6.5A3.5 3.5 0 0 0 5 0zm0 5a1.4 1.4 0 1 1 0-2.8A1.4 1.4 0 0 1 5 5z" fill="#fff"/></svg></span><span class="contact-item__label">Address</span><span class="contact-item__text">Lorem ipsum dolor sit amet,<br>consectetur adipiscing 952</span></div>
    <div class="contact-rule" style="top:56px"></div>
    <div class="contact-item" style="top:62px"><span class="contact-item__icon"><svg width="5" height="5" viewBox="0 0 10 10"><path d="M2 0.5l2 2-1 1.5c.6 1.3 1.6 2.3 3 3l1.5-1 2 2-1.2 1.5C4.5 9.3.7 5.5.5 1.7z" fill="#fff"/></svg></span><span class="contact-item__label">Phone</span><span class="contact-item__text">+1-555-010-2040</span></div>
    <div class="contact-rule" style="top:80px"></div>
    <div class="contact-item" style="top:86px"><span class="contact-item__icon"><svg width="5" height="5" viewBox="0 0 10 8"><path d="M0 0h10v8H0z" fill="#fff"/><path d="M0 0l5 4 5-4" stroke="#121212" stroke-width="1" fill="none"/></svg></span><span class="contact-item__label">Email Address</span><span class="contact-item__text">info@vigorhealthco.com</span></div>
    <div class="footer-divider"></div>
    <div class="footer-badge abs"><span>MAEBEL VIGOR FITNESS</span></div>
    <span class="social" style="left:250px"></span>
    <span class="social" style="left:262px"></span>
    <span class="social" style="left:274px"></span>
    <p class="copyright abs">Copyright 2024 - Vigor Health &amp; Fitness.<br>All Rights Reserved</p>
  </footer>
</article>

<!-- DARK THEME -->
<article class="page page--dark">
  <header class="site-header abs">
    <p class="site-header__name abs">MAEBEL VIGOR FITNESS FOR MEN !</p>
    <a class="btn btn--primary header-btn">Buy Now <i></i></a>
  </header>
  <div class="brand-badge abs"><span>MAEBEL VIGOR FITNESS</span></div>

  <section class="hero abs" role="img" aria-label="Woman smiling in a glowing outdoor hot tub at night"></section>
  <p class="hero__kicker abs">Top of the Line Health Products Exclusively for the Financially Successful</p>
  <h1 class="hero__title display abs">Dramatically Improve Your<br><span class="accent">Health</span> Without <span class="accent">Exercise</span></h1>
  <p class="hero__lead abs">Successful Men Recognize the Importance of Their Health and Make it a Priority.&nbsp; It’s Your Time.&nbsp; You’ve Earned it.</p>
  <a class="btn btn--primary hero__btn abs">Buy Now <i></i></a>
  <svg class="hero-wave abs" viewBox="0 0 344 60" preserveAspectRatio="none">
    <path d="M0 26 C60 14 140 12 230 34 C280 46 320 30 344 10 L344 60 L0 60 Z" fill="#050505"/>
    <defs><linearGradient id="gd1" x1="0" x2="1"><stop offset="0" stop-color="#f58220"/><stop offset="1" stop-color="#e8401c"/></linearGradient></defs>
    <path d="M108 8 C160 10 185 38 235 40 C285 42 320 24 344 6 C322 30 288 50 235 50 C182 50 160 20 108 8 Z" fill="url(#gd1)"/>
  </svg>

  <div class="product__ring ring--left abs" style="left:33px;top:216px"></div>
  <div class="product__media media--sauna" style="left:38px;top:221px" role="img" aria-label="Couple in white robes sitting in a wooden sauna"></div>
  <h2 class="product__title display" style="left:172px;top:238px">Sau<span class="accent">nas</span></h2>
  <p class="product__sub" style="left:172px;top:256px">Lorem ipsum dolor sit amet, consectetur adipiscing.</p>
  <p class="product__body" style="left:172px;top:266px">Sed ut perspiciatis unde omnis iste natus error sit voluptatem accusantium doloremque laudantium, totam rem aperiam, eaque ipsa quae ab illo inventore veritatis et quasi architecto beatae vitae dicta sunt explicabo. Nemo enim ipsam voluptatem quia voluptas sit aspernatur aut odit aut fugit, sed quia consequuntur.</p>
  <a class="btn btn--primary btn--sm" style="left:172px;top:309px">Buy Now <i></i></a>
  <a class="btn btn--ghost btn--supplier" style="left:213px;top:309px">Buy From Supplier <i></i></a>

  <div class="product__ring ring--right abs" style="left:180px;top:336px"></div>
  <div class="product__media media--plunge" style="left:185px;top:341px" role="img" aria-label="Woman relaxing in a bubbling cold plunge tub"></div>
  <h2 class="product__title display" style="left:41px;top:358px">Cold <span class="accent-o">Plunge</span> Tubs</h2>
  <p class="product__sub" style="left:41px;top:376px">Lorem ipsum dolor sit amet, consectetur adipiscing.</p>
  <p class="product__body" style="left:41px;top:386px">Sed ut perspiciatis unde omnis iste natus error sit voluptatem accusantium doloremque laudantium, totam rem aperiam, eaque ipsa quae ab illo inventore veritatis et quasi architecto beatae vitae dicta sunt explicabo. Nemo enim ipsam voluptatem quia voluptas sit aspernatur aut odit aut fugit, sed quia consequuntur.</p>
  <a class="btn btn--primary btn--sm" style="left:41px;top:430px">Buy Now <i></i></a>
  <a class="btn btn--ghost btn--supplier" style="left:83px;top:430px">Buy From Supplier <i></i></a>

  <div class="product__ring ring--left abs" style="left:33px;top:457px"></div>
  <div class="product__media media--chair" style="left:38px;top:462px" role="img" aria-label="Man seated in a black massage chair"></div>
  <h2 class="product__title display" style="left:172px;top:478px"><span class="accent">Massage</span> Chairs</h2>
  <p class="product__sub" style="left:172px;top:496px">Lorem ipsum dolor sit amet, consectetur adipiscing.</p>
  <p class="product__body" style="left:172px;top:506px">Sed ut perspiciatis unde omnis iste natus error sit voluptatem accusantium doloremque laudantium, totam rem aperiam, eaque ipsa quae ab illo inventore veritatis et quasi architecto beatae vitae dicta sunt explicabo. Nemo enim ipsam voluptatem quia voluptas sit aspernatur aut odit aut fugit, sed quia consequuntur.</p>
  <a class="btn btn--primary btn--sm" style="left:172px;top:549px">Buy Now <i></i></a>
  <a class="btn btn--ghost btn--supplier" style="left:211px;top:549px">Buy From Supplier <i></i></a>

  <section class="benefits abs">
    <div class="benefits__figure-left abs" role="img" aria-label="Man soaking in an ice bath"></div>
    <div class="benefits__figure-right abs" role="img" aria-label="Woman reclining in a massage chair"></div>
    <h2 class="benefits__title display abs">When there’s no time for exercise. Use <span class="accent-o">Hot,</span> <span class="accent">Cold,</span> or<br><span class="accent-o">Massage</span>. The benefits are numerous.</h2>
    <p class="benefits__list abs">Relieve Stress&nbsp; -&nbsp; Detox Your Pores&nbsp; -&nbsp; Sleep Better<br>Relieve Muscle Tension&nbsp; -&nbsp; Boost Energy Levels<br>Increase Testosterone&nbsp; -&nbsp; Reduce Inflammation&nbsp; -&nbsp; Increase Immunity&nbsp; Reduce<br>Depression Alleviate Joint Pain&nbsp; -&nbsp; Healthier Skin<br>Lower the Risk of Cardiovascular Disease&nbsp; -&nbsp; Increase Metabolism<br>Promote Weight Loss&nbsp; -&nbsp; A Longer &amp; Healthier Life</p>
    <p class="benefits__note abs">Specific Improvements will be Individual to You.</p>
    <a class="btn btn--primary benefits__btn">Buy Now <i></i></a>
  </section>

  <h2 class="testimonials__title display abs"><span class="accent">Client</span> Testimonials</h2>
  <div class="quote" style="left:48px;top:796px"><span class="quote__mark quote__mark--open">“</span><span class="quote__stars">★★★★★</span><p>I climb in my sauna half asleep every morning for twenty minutes. It wakes me up better than coffee ever did. Perfect morning start.</p><span class="quote__mark quote__mark--close">”</span></div>
  <div class="quote" style="left:174px;top:796px"><span class="quote__mark quote__mark--open">“</span><span class="quote__stars">★★★★★</span><p>I love a good massage but booking one is hard. The chair is always there. I forget about work and usually drift off.</p><span class="quote__mark quote__mark--close">”</span></div>
  <div class="quote" style="left:48px;top:838px"><span class="quote__mark quote__mark--open">“</span><span class="quote__stars">★★★★★</span><p>My massage chair saves my back. I dial in a deep massage or gentle pressure whenever I need it. Worth every penny.</p><span class="quote__mark quote__mark--close">”</span></div>
  <div class="quote" style="left:174px;top:838px"><span class="quote__mark quote__mark--open">“</span><span class="quote__stars">★★★★★</span><p>I hate exercise and love my work. I have the dual plunge, hot and cold. The cold is refreshing in summer, hot in winter.</p><span class="quote__mark quote__mark--close">”</span></div>
  <div class="quote" style="left:48px;top:880px"><span class="quote__mark quote__mark--open">“</span><span class="quote__stars">★★★★★</span><p>A sauna at home is a game changer. After a long day the heat melts my stress. A mini vacation without leaving home.</p><span class="quote__mark quote__mark--close">”</span></div>
  <div class="quote" style="left:174px;top:880px"><span class="quote__mark quote__mark--open">“</span><span class="quote__stars">★★★★★</span><p>I am forty three with arthritis. My cold plunge rejuvenates my body. A natural way to deal with joint pain that actually works.</p><span class="quote__mark quote__mark--close">”</span></div>
  <div class="quote" style="left:48px;top:922px"><span class="quote__mark quote__mark--open">“</span><span class="quote__stars">★★★★★</span><p>Before my chair I walked like an old man. Every step was effort. Now I get real relief every single evening at home.</p><span class="quote__mark quote__mark--close">”</span></div>
  <div class="quote" style="left:174px;top:922px"><span class="quote__mark quote__mark--open">“</span><span class="quote__stars">★★★★★</span><p>At sixty three my body gets stiff after driving. I climb out of the car hunched. My massage chair fixes my lower back.</p><span class="quote__mark quote__mark--close">”</span></div>
  <p class="testimonials__note abs">Everything Works Better with Increased Blood Flow</p>
  <a class="btn btn--primary testimonials__btn">Buy Now <i></i></a>

  <svg class="footer-wave abs" viewBox="0 0 344 50" preserveAspectRatio="none">
    <defs><linearGradient id="gd2" x1="0" x2="1"><stop offset="0" stop-color="#f58220"/><stop offset="1" stop-color="#e8401c"/></linearGradient></defs>
    <path d="M0 44 C70 14 150 8 230 26 C280 36 315 34 344 26 L344 50 L0 50 Z" fill="#121212"/>
    <path d="M2 40 C70 4 160 0 240 18 C290 28 320 26 344 20 C318 32 285 36 240 28 C160 12 80 14 2 40 Z" fill="url(#gd2)"/>
  </svg>
  <footer class="site-footer abs">
    <p class="footer__label" style="left:41px;top:20px">Contact Me</p>
    <div class="field" style="top:31px">Name</div>
    <div class="field" style="top:45px">Email</div>
    <div class="field" style="top:59px">Phone</div>
    <div class="field" style="top:73px">Message</div>
    <a class="btn btn--primary submit">Submit Now</a>
    <p class="footer__label" style="left:140px;top:20px">Contact Details</p>
    <div class="contact-item" style="top:33px"><span class="contact-item__icon"><svg width="5" height="5" viewBox="0 0 10 10"><path d="M5 0a3.5 3.5 0 0 0-3.5 3.5C1.5 6 5 10 5 10s3.5-4 3.5-6.5A3.5 3.5 0 0 0 5 0zm0 5a1.4 1.4 0 1 1 0-2.8A1.4 1.4 0 0 1 5 5z" fill="#fff"/></svg></span><span class="contact-item__label">Address</span><span class="contact-item__text">Lorem ipsum dolor sit amet,<br>consectetur adipiscing 952</span></div>
    <div class="contact-rule" style="top:56px"></div>
    <div class="contact-item" style="top:62px"><span class="contact-item__icon"><svg width="5" height="5" viewBox="0 0 10 10"><path d="M2 0.5l2 2-1 1.5c.6 1.3 1.6 2.3 3 3l1.5-1 2 2-1.2 1.5C4.5 9.3.7 5.5.5 1.7z" fill="#fff"/></svg></span><span class="contact-item__label">Phone</span><span class="contact-item__text">+1-555-010-2040</span></div>
    <div class="contact-rule" style="top:80px"></div>
    <div class="contact-item" style="top:86px"><span class="contact-item__icon"><svg width="5" height="5" viewBox="0 0 10 8"><path d="M0 0h10v8H0z" fill="#fff"/><path d="M0 0l5 4 5-4" stroke="#121212" stroke-width="1" fill="none"/></svg></span><span class="contact-item__label">Email Address</span><span class="contact-item__text">info@vigorhealthco.com</span></div>
    <div class="footer-divider"></div>
    <div class="footer-badge abs"><span>MAEBEL VIGOR FITNESS</span></div>
    <span class="social" style="left:250px"></span>
    <span class="social" style="left:262px"></span>
    <span class="social" style="left:274px"></span>
    <p class="copyright abs">Copyright 2024 - Vigor Health &amp; Fitness.<br>All Rights Reserved</p>
  </footer>
</article>

</body>
</html>
```